Business Card For Halvenmoor Financial Consulting

Hi, I would like a business card designed. Bold, modern.
Please use the same design as the logo. I have also attached the website design to see the overall theme.
Wordmark Font
Color: Hex: #01AEF7

```html
<!DOCTYPE html>
<html lang="en">
<head>
<meta charset="utf-8">
<title>Halvenmoor Financial Consulting – Business Card</title>
<link rel="stylesheet" href="https://fonts.googleapis.com/css2?family=Montserrat:wght@700;800&family=Lato:wght@400;700&display=swap">
<style>
  :root {
    --brand-blue: #01aef7;
    --card-ink: #0e1620;
    --card-ink-deep: #0a1118;
    --paper-white: #f2f4f6;
    --muted-line: #5b6670;
    --backdrop: #4b4b4c;
  }
  * { box-sizing: border-box; margin: 0; padding: 0; }
  html, body { width: 1200px; height: 911px; overflow: hidden; }
  body {
    background: var(--backdrop);
    font-family: "Lato", Arial, sans-serif;
    position: relative;
  }
  .card {
    position: absolute;
    width: 540px;
    height: 309px;
    background: var(--card-ink);
    overflow: hidden;
  }
  .card--back { left: 70px; top: 92px; }
  .card--front { left: 590px; top: 470px; }

  .back-pattern {
    position: absolute;
    inset: 0;
    background: linear-gradient(100deg, #3f8fc4 0%, #24557a 18%, #142433 42%, var(--card-ink-deep) 70%, var(--card-ink-deep) 100%);
  }

  .brand {
    position: absolute;
    left: 0; right: 0; top: 62px;
    display: flex;
    align-items: center;
    justify-content: center;
    gap: 14px;
  }
  .brand__square {
    width: 40px; height: 40px;
    border: 4px solid var(--brand-blue);
    flex: none;
  }
  .brand__name {
    font-family: "Montserrat", Arial, sans-serif;
    font-weight: 800;
    font-size: 21px;
    line-height: 1.1;
    letter-spacing: 0.5px;
    color: #ffffff;
    text-transform: uppercase;
  }

  .details {
    position: absolute;
    left: 0; right: 0; top: 150px;
    display: flex;
    justify-content: center;
    align-items: center;
  }
  .person {
    text-align: right;
    padding-right: 16px;
    color: #ffffff;
  }
  .person__name {
    font-family: "Montserrat", Arial, sans-serif;
    font-weight: 800;
    font-size: 17px;
    letter-spacing: 0.5px;
    text-transform: uppercase;
  }
  .person__title {
    font-size: 15px;
    color: var(--brand-blue);
    margin-top: 2px;
  }
  .person__address {
    font-size: 12.5px;
    line-height: 1.35;
    margin-top: 3px;
  }
  .divider {
    width: 1px;
    height: 96px;
    background: var(--muted-line);
  }
  .contacts {
    list-style: none;
    padding-left: 16px;
    color: #ffffff;
    font-size: 12.5px;
    line-height: 1.5;
  }
  .contacts li { display: flex; align-items: center; gap: 8px; }
  .contacts svg { width: 10px; height: 10px; flex: none; }

  .stripe {
    position: absolute;
    left: 0; right: 0; bottom: 0;
    height: 11px;
    display: flex;
  }
  .stripe__blue { flex: 0 0 76%; background: var(--brand-blue); }
  .stripe__white { flex: 1; background: var(--paper-white); }
</style>
</head>
<body>

<section class="card card--back" aria-label="Card back">
  <div class="back-pattern" role="img" aria-label="Repeating brand pattern fading from bright blue foil to dark embossing"></div>
</section>

<section class="card card--front" aria-label="Card front">
  <div class="brand">
    <span class="brand__square" aria-hidden="true"></span>
    <span class="brand__name">Halvenmoor<br>Financial Consulting</span>
  </div>

  <div class="details">
    <div class="person">
      <p class="person__name">Owen Carradine</p>
      <p class="person__title">Founder &amp; CEO</p>
      <p class="person__address">Your Address<br>City, State, Zip 1235</p>
    </div>
    <span class="divider" aria-hidden="true"></span>
    <ul class="contacts">
      <li>
        <svg viewBox="0 0 10 10" aria-hidden="true"><path d="M2 1l2 2-1 1.2c.6 1.2 1.5 2.1 2.8 2.8L7 6l2 2-1.2 1.2C4.5 9 1 5.5.8 2.2z" fill="var(--brand-blue)"/></svg>
        (555) 310-4821
      </li>
      <li>
        <svg viewBox="0 0 10 10" aria-hidden="true"><rect x="2.5" y="0.5" width="5" height="9" rx="1" fill="none" stroke="var(--brand-blue)" stroke-width="1.2"/><circle cx="5" cy="8" r="0.6" fill="var(--brand-blue)"/></svg>
        (555) 310-4822
      </li>
      <li>
        <svg viewBox="0 0 10 10" aria-hidden="true"><rect x="0.5" y="2" width="9" height="6" fill="var(--brand-blue)"/><path d="M0.5 2L5 5.5 9.5 2" fill="none" stroke="var(--card-ink)" stroke-width="0.9"/></svg>
        info@halvenmoorconsulting.com
      </li>
      <li>
        <svg viewBox="0 0 10 10" aria-hidden="true"><circle cx="5" cy="5" r="4.3" fill="none" stroke="var(--brand-blue)" stroke-width="1.1"/><path d="M.8 5h8.4M5 .7c-2.2 2.6-2.2 6 0 8.6M5 .7c2.2 2.6 2.2 6 0 8.6" fill="none" stroke="var(--brand-blue)" stroke-width="0.8"/></svg>
        halvenmoorconsulting.com
      </li>
    </ul>
  </div>

  <div class="stripe" aria-hidden="true">
    <span class="stripe__blue"></span>
    <span class="stripe__white"></span>
  </div>
</section>

</body>
</html>
```